"Harbor Builders" is a residential building company and needs a new business card design and may re

We would like a redesign based on the existing logo, and would like to see a new font as well. We are bespoke home builders who build sustainable energy efficient homes.

Industry/Entity Type

Construction

Contact Information for Business Card

Business card size 40mm x 90mm

Colors

Designer to choose colors to be used in the design.

```html
<!DOCTYPE html>
<html lang="en">
<head>
<meta charset="utf-8">
<title>Harbor Builders – Business Card</title>
<link rel="stylesheet" href="https://fonts.googleapis.com/css2?family=Roboto:wght@400;500;700&family=Roboto+Condensed:wght@700&display=swap">
<style>
  :root {
    --backdrop: #5b4a3a;
    --card-white: #f3f3f3;
    --ink: #0b0b0b;
    --text-grey: #3c3c3c;
    --lime: #b2cb2b;
    --card-black: #060708;
    --rule-grey: #9a9a9a;
    --white: #ffffff;
  }
  * { margin: 0; padding: 0; box-sizing: border-box; }
  html, body { width: 1200px; height: 960px; overflow: hidden; }
  body {
    position: relative;
    background: var(--backdrop);
    font-family: "Roboto", Arial, sans-serif;
  }

  /* Front card */
  .card-front {
    position: absolute;
    left: 314px; top: 113px;
    width: 600px; height: 342px;
    background: var(--card-white);
    overflow: hidden;
  }
  .card-front .accent-line {
    position: absolute; left: 0; top: 324px;
    width: 100%; height: 3px; background: var(--lime);
  }
  .card-front .base-band {
    position: absolute; left: 0; top: 327px;
    width: 100%; height: 15px; background: var(--ink);
  }
  .brand-front {
    position: absolute; left: 36px; top: 148px;
    display: flex; align-items: center; gap: 12px;
  }
  .brand-mark {
    width: 26px; height: 26px; background: var(--lime);
  }
  .brand-name {
    font-family: "Roboto", Arial, sans-serif;
    font-weight: 500; font-size: 28px; color: var(--ink);
    letter-spacing: -0.3px;
  }
  .divider {
    position: absolute; left: 296px; top: 72px;
    width: 1px; height: 206px;
    background: linear-gradient(to bottom, transparent, var(--rule-grey) 20%, var(--rule-grey) 80%, transparent);
  }
  .contact-block {
    position: absolute; left: 320px; top: 76px;
    color: var(--text-grey); font-size: 14.5px; line-height: 19px;
  }
  .person-name {
    font-family: "Roboto Condensed", "Arial Narrow", sans-serif;
    font-weight: 700; font-size: 21px; color: var(--ink);
    line-height: 26px; margin-bottom: 12px;
  }
  .company-name { font-weight: 700; font-size: 13.5px; }
  .address { margin-bottom: 0; }
  .registration { margin-top: 3px; }
  .contact-list { list-style: none; margin-top: 5px; }
  .contact-list li { display: flex; align-items: center; gap: 8px; height: 19px; }
  .contact-list svg { width: 14px; height: 14px; flex: none; fill: var(--ink); }

  /* Back card */
  .card-back {
    position: absolute;
    left: 311px; top: 472px;
    width: 600px; height: 342px;
    background: var(--card-black);
  }
  .brand-back {
    position: absolute; left: 0; right: 0; top: 120px;
    display: flex; justify-content: center; align-items: center; gap: 18px;
  }
  .brand-back .brand-mark { width: 44px; height: 44px; }
  .brand-back .brand-name { color: var(--white); font-size: 48px; }
  .web-address {
    position: absolute; left: 0; right: 0; top: 296px;
    text-align: center; color: var(--white);
    font-size: 14px; letter-spacing: 3.2px;
  }
</style>
</head>
<body>
  <section class="card-front">
    <div class="brand-front">
      <span class="brand-mark"></span>
      <span class="brand-name">Harbor Builders</span>
    </div>
    <div class="divider"></div>
    <div class="contact-block">
      <h1 class="person-name">DANIEL MORROW</h1>
      <p class="company-name">Harbor Builders Pty Ltd</p>
      <p class="address">PO Box 4120 Northgate<br>LPO Eastvale WA 6091</p>
      <p class="registration">Registration 48305<br>ABN: 42 305 918 276</p>
      <ul class="contact-list">
        <li><svg viewBox="0 0 14 14"><path d="M4 0h6a1 1 0 0 1 1 1v12a1 1 0 0 1-1 1H4a1 1 0 0 1-1-1V1a1 1 0 0 1 1-1zm0.5 1.5v9h5v-9z"/></svg>0400 555 018</li>
        <li><svg viewBox="0 0 14 14"><path d="M1 3h12v8H1z M1 3l6 4.5L13 3" fill="none" stroke="#0b0b0b" stroke-width="1.4"/><path d="M1 3h12L7 7.5z"/></svg>daniel@harborbuilders.com.au</li>
        <li><svg viewBox="0 0 14 14"><circle cx="7" cy="7" r="6"/><path d="M4 4.5c1.5-.5 2.5.5 2 1.5s-2 .5-2 2 1.5 1.5 1 3M9 3c0 1.5 1.5 1.5 2.5 2.5M9 11c0-1.5 1-2 2-2" fill="none" stroke="#f3f3f3" stroke-width="1.1"/></svg>www.harborbuilders.com.au</li>
      </ul>
    </div>
    <div class="accent-line"></div>
    <div class="base-band"></div>
  </section>

  <section class="card-back">
    <div class="brand-back">
      <span class="brand-mark"></span>
      <span class="brand-name">Harbor Builders</span>
    </div>
    <p class="web-address">www.harborbuilders.com.au</p>
  </section>
</body>
</html>
```